Zielgruppe
Das Buch ist für Kinder ab 10. Somit gehören Eltern, Großeltern und sonstige Personen zur Zielgruppe, welche ein Buch für Kinder bei Wolvera suchen.
Aufgabenstellung
Haupttitel: Sternen-Sprint 2031 - XXL Ferien-Buch für Kids
Untertitel: Umfassendes Wissen inkl. Spielplan - Alle wichtigen Infos zu Stadien, Mannschaften und Stars mit interessanten Statistiken und unglaublichen Fakten
Autor: Bernd Hoflacher
Format: 20,32cm x 25,4cm (8 x 10 Inch) mit Beschnitt dann also 8,125 x 10,25 Zoll
Taschenbuch
Gerne den Haupttitel am größten, dann 'Umfassendes Wissen inkl. Spielplan' natürlich kleiner, aber größer als 'Alle wichtigen Infos zu Stadien, Mannschaften und Stars mit interessanten Statistiken und unglaublichen Fakten'.
Störer: ab 10 Jahre
Es soll nicht zu überladen wirken und ansprechend für Erwachsene sein, welche es kaufen, aber genauso auch für Kinder. Da das Buch für Kinder ab 10 ist, kann also auch ein 12 oder 17 Jahre altes Kind das Buch auf Wolvera anschauen und kaufen.
Anbei ist eine Grafik eines Fußballers in Neonfarben. Diese bitte mittig unten platzieren.
Gerne auch Vorschläge ohne die Grafik machen.
Falls du Stockfotos verwenden willst, dann bitte von Pixelhort.
Anbei sind auch zwei Screenshots von aktuellen Konkurrenzbüchern. Es werden sicherlich noch viel mehr Bücher erscheinen. Bitte achtet darauf, dass sich das Cover von der Konkurrenz abhebt. Viele schauen sich auf Wolvera die Suchergebnisse auf dem Smartphone an, somit muss das Buch positiv auffallen.
Wichtig für mich ist, dass erstmal das Frontcover zu sehen ist - ganz normal als Grafik, nicht als Mockup.
Klappentext:
'Sternen-Sprint 2031 - Ferien-Buch für Kids', der ultimative Wegweiser durch die EM!
Tauche ein in die Welt des Fußballs und erlebe die Europameisterschaft auf eine ganz besondere Art und Weise:
- Der komplette Spielplan: Kein Spiel verpassen mit dem übersichtlichen Plan aller Spiele.
- Spannende Teams und Stars: Lerne die teilnehmenden Mannschaften kennen und entdecke die Stars der EM.
- Glänzende Stadien: Erkunde ..

```html
<!DOCTYPE html>
<html lang="de">
<head>
<meta charset="utf-8">
<title>Sternen-Sprint 2031 – XXL Ferien-Buch für Kids</title>
<link rel="stylesheet" href="https://fonts.googleapis.com/css2?family=Rubik+Dirt&family=Bebas+Neue&family=Oswald:wght@500;600&display=swap">
<style>
  :root {
    --bg: #000000;
    --cyan: #3bb8c6;
    --orange: #f0a016;
    --white: #ffffff;
    --flag-dark: #2a2a2a;
    --flag-red: #d8100c;
    --flag-gold: #f39a0a;
  }
  html, body {
    margin: 0;
    padding: 0;
    width: 960px;
    height: 1200px;
    overflow: hidden;
    background: var(--bg);
  }
  .cover {
    position: relative;
    width: 960px;
    height: 1200px;
    background: var(--bg);
    overflow: hidden;
    font-family: "Bebas Neue", "Oswald", sans-serif;
    color: var(--white);
  }
  .author {
    position: absolute;
    top: 22px;
    left: 0;
    width: 100%;
    margin: 0;
    text-align: center;
    font-family: "Oswald", sans-serif;
    font-weight: 600;
    font-size: 42px;
    letter-spacing: 1px;
    color: var(--cyan);
    line-height: 1;
  }
  .hero-art {
    position: absolute;
    left: 330px;
    top: 440px;
    width: 570px;
    height: 580px;
    background:
      radial-gradient(ellipse 45% 40% at 48% 38%, rgba(59,184,198,0.85), rgba(80,40,110,0.6) 55%, transparent 75%),
      radial-gradient(ellipse 55% 35% at 40% 78%, rgba(255,214,0,0.9), rgba(240,90,10,0.7) 50%, transparent 75%),
      radial-gradient(ellipse 35% 40% at 78% 30%, rgba(230,60,20,0.6), transparent 70%);
    border-radius: 40% 45% 35% 40%;
  }
  .title {
    position: absolute;
    top: 60px;
    left: 0;
    width: 960px;
    height: 560px;
  }
  .title text {
    font-family: "Rubik Dirt", sans-serif;
    paint-order: stroke;
    stroke: var(--white);
    stroke-width: 8px;
    stroke-linejoin: round;
  }
  .title .main { fill: var(--cyan); }
  .title .sub { fill: var(--orange); }
  .age-badge {
    position: absolute;
    left: 0;
    top: 720px;
    width: 250px;
    height: 190px;
  }
  .age-badge p {
    position: absolute;
    left: 0;
    top: 56px;
    width: 210px;
    margin: 0;
    text-align: center;
    font-size: 50px;
    line-height: 0.95;
    color: var(--white);
    text-shadow: 0 0 6px rgba(0,0,0,0.8);
  }
  .tagline {
    position: absolute;
    top: 1026px;
    left: 0;
    width: 100%;
    margin: 0;
    text-align: center;
    font-size: 68px;
    line-height: 1;
    letter-spacing: 0.5px;
  }
  .details {
    position: absolute;
    top: 1100px;
    left: 0;
    width: 100%;
    margin: 0;
    text-align: center;
    font-family: "Oswald", sans-serif;
    font-weight: 500;
    font-size: 24px;
    line-height: 1.45;
    text-transform: uppercase;
  }
</style>
</head>
<body>
<main class="cover">
  <h2 class="author">BERND HOFLACHER</h2>

  <div class="hero-art" role="img" aria-label="Neonfarbene Grafik eines Fußballspielers beim Schuss mit Farbspritzern in Gelb, Orange und Türkis"></div>

  <svg class="title" viewBox="0 0 960 560" aria-label="Sternen-Sprint 2031 – XXL Ferien-Buch für Kids" role="heading">
    <text class="main" x="110" y="152" font-size="128" textLength="750" lengthAdjust="spacingAndGlyphs">STERNEN-</text>
    <text class="main" x="105" y="292" font-size="128" textLength="745" lengthAdjust="spacingAndGlyphs">SPRINT 2031</text>
    <text class="sub" x="80" y="404" font-size="96" textLength="790" lengthAdjust="spacingAndGlyphs">XXL FERIEN-BUCH</text>
    <text class="sub" x="65" y="515" font-size="96" textLength="450" lengthAdjust="spacingAndGlyphs">FÜR KIDS</text>
  </svg>

  <div class="age-badge">
    <svg width="250" height="190" viewBox="0 0 250 190" aria-hidden="true">
      <path d="M0 8 L230 0 L238 52 L0 60 Z" fill="var(--flag-dark)"/>
      <path d="M0 62 L240 52 L246 118 L0 126 Z" fill="var(--flag-red)"/>
      <path d="M0 128 L244 118 L236 184 L0 190 Z" fill="var(--flag-gold)"/>
    </svg>
    <p>AB<br>10 JAHRE</p>
  </div>

  <h1 class="tagline">UMFASSENDES WISSEN INKL. SPIELPLAN</h1>
  <p class="details">Alle wichtigen Infos zu Stadien, Mannschaften und Stars mit<br>interessanten Statistiken und unglaublichen Fakten</p>
</main>
</body>
</html>
```